Equipment Finance Specialist I work with companies who need the funds to buy their equipment

I would like a business card that stands out on the shelves. I want to be able to hand it to someone and say WOW. This card should have my logo.
You can put color into it I am very open on design and color

What my company does is we deal with dealerships that sell equipment such as Dump Trucks garbage trucks tractors trailers. Customers get referred to us and depending on their time in business we will ask for the following items

Companies that have been in business for more than two years we have a credit application program up to 250K . With this program we need the following items Credit application filled out(which is what I would like to be able for the customer to click on my website to get.) as well as three current month bank statements.

Deals over 250k we will need the following items

2 years business tax returns
2 years personal tax returns
Profit & Loss statement
Personal Financial Statement

what we do
100% FINANCING
SEASONAL PAYMENTS
LOAN BALLOON PAYMENTS
TRAC LEASING
LOW-INTEREST REFINANCING RATES
DEBT CONSOLIDATION

We specialize in creative financing solutions and offer a variety of reliable, flexible and expandable lending choices.

Target Market(s)

Trucking Companies

Industry/Entity Type

Trucking Company

Contact Information for Business Card

* $250,000 Application only Program
* Loans from $30,000 to 5,000,000
* Competitive Interest Rates

Font styles to use
Serif
Sans Serif

Colors

Designer to choose colors to be used in the design.

Requirements
Must have
• On the back of the card.
• * $250,000 Application only Program
• * Loans from $30,000 to 5,000,000
• My name, email, website. address
• * Competitive Interest Rates
• * 100% Financing
Nice to have
• I want my logo to pop on the card
• My logo is the great one I would like to use
Should not have
• I am up for your creativity as well

```html
<!DOCTYPE html>
<html lang="en">
<head>
<meta charset="utf-8">
<title>Summit Lending – Business Card</title>
<link rel="stylesheet" href="https://fonts.googleapis.com/css2?family=Work+Sans:wght@400;500;700;800&display=swap">
<style>
  :root {
    --navy: #1e2d64;
    --red: #e01e2e;
    --white: #ffffff;
    --stage: #2a2c2e;
    --ink: #1e2d64;
    --soft: rgba(255,255,255,.82);
  }
  * { box-sizing: border-box; margin: 0; padding: 0; }
  html, body { width: 1200px; height: 738px; overflow: hidden; }
  body {
    background: var(--stage);
    font-family: "Work Sans", Arial, sans-serif;
    position: relative;
  }
  .card {
    position: absolute;
    width: 520px;
    height: 298px;
    top: 220px;
    overflow: hidden;
    box-shadow: 0 10px 30px rgba(0,0,0,.45);
  }
  .card--front { left: 60px; background: var(--navy); }
  .card--back { left: 620px; background: var(--white); }

  .brand {
    display: flex;
    align-items: center;
    gap: 10px;
    font-weight: 800;
    text-transform: uppercase;
    letter-spacing: .5px;
    white-space: nowrap;
  }
  .brand__dot { border-radius: 50%; flex: none; }

  .card--front .brand {
    position: absolute;
    left: 50%; top: 112px;
    transform: translate(-50%, -50%);
    color: var(--white);
    font-size: 34px;
  }
  .card--front .brand__dot { width: 52px; height: 52px; background: var(--white); }

  .offers {
    position: absolute;
    left: 40px; right: 40px; top: 178px;
    list-style: none;
    display: grid;
    grid-template-columns: 1fr 1fr;
    gap: 10px 24px;
    color: var(--soft);
    font-size: 12.5px;
    letter-spacing: .3px;
  }
  .offers li { display: flex; align-items: center; gap: 8px; }
  .offers li::before {
    content: "";
    width: 6px; height: 6px;
    background: var(--red);
    border-radius: 50%;
    flex: none;
  }

  .card--back .brand {
    position: absolute;
    left: 26px; top: 40px;
    color: var(--navy);
    font-size: 21px;
    gap: 8px;
  }
  .card--back .brand__dot { width: 32px; height: 32px; background: var(--navy); }

  .person {
    position: absolute;
    right: 26px; top: 40px;
    text-align: right;
  }
  .person__name {
    color: var(--red);
    font-size: 21px;
    font-weight: 500;
    letter-spacing: .3px;
    text-transform: uppercase;
  }
  .person__role { color: var(--ink); font-size: 12.5px; margin-top: 1px; }

  .divider {
    position: absolute;
    left: 26px; right: 26px; top: 104px;
    height: 1.5px;
    background: var(--navy);
  }

  .contacts {
    position: absolute;
    left: 26px; top: 118px;
    list-style: none;
    color: var(--ink);
    font-size: 13.5px;
    letter-spacing: .4px;
  }
  .contacts li { display: flex; align-items: center; gap: 10px; height: 19px; }
  .contacts svg { width: 10px; height: 10px; flex: none; }

  .wave { position: absolute; left: 0; top: 0; width: 520px; height: 298px; }

  .address {
    position: absolute;
    right: 26px; bottom: 40px;
    text-align: right;
    color: var(--white);
    font-size: 13px;
    letter-spacing: .6px;
    line-height: 1.45;
  }
</style>
</head>
<body>
  <section class="card card--front" aria-label="Card front">
    <div class="brand"><span class="brand__dot"></span>Summit Lending</div>
    <ul class="offers">
      <li>$250,000 Application Only Program</li>
      <li>Loans from $30,000 to $5,000,000</li>
      <li>Competitive Interest Rates</li>
      <li>100% Financing</li>
    </ul>
  </section>

  <section class="card card--back" aria-label="Card back">
    <svg class="wave" viewBox="0 0 520 298" aria-hidden="true">
      <path d="M0,196 C170,228 340,152 520,136 L520,298 L0,298 Z" fill="var(--red)"/>
      <path d="M0,248 C170,262 340,172 520,148 L520,298 L0,298 Z" fill="var(--white)"/>
      <path d="M0,260 C170,274 340,184 520,158 L520,298 L0,298 Z" fill="var(--navy)"/>
    </svg>

    <div class="brand"><span class="brand__dot"></span>Summit Lending</div>

    <div class="person">
      <div class="person__name">Daniel Harper</div>
      <div class="person__role">Director</div>
    </div>

    <div class="divider"></div>

    <ul class="contacts">
      <li>
        <svg viewBox="0 0 10 10"><path d="M2,0.5 L4,3 L3,4 C3.6,5.4 4.6,6.4 6,7 L7,6 L9.5,8 L8.5,9.5 C4.5,9.2 0.8,5.5 0.5,1.5 Z" fill="var(--red)"/></svg>
        1300 472 915
      </li>
      <li>
        <svg viewBox="0 0 10 10"><rect x="0.6" y="2" width="8.8" height="6" fill="none" stroke="var(--red)" stroke-width="1"/><path d="M0.6,2 L5,5.5 L9.4,2" fill="none" stroke="var(--red)" stroke-width="1"/></svg>
        info@summitlending.com
      </li>
      <li>
        <svg viewBox="0 0 10 10"><circle cx="5" cy="5" r="4.3" fill="none" stroke="var(--red)" stroke-width="1"/><ellipse cx="5" cy="5" rx="1.8" ry="4.3" fill="none" stroke="var(--red)" stroke-width=".8"/><path d="M0.7,5 H9.3" stroke="var(--red)" stroke-width=".8"/></svg>
        www.summitlending.com
      </li>
    </ul>

    <div class="address">2185 Ridgefield Dr.<br>Austin, TX 78701</div>
  </section>
</body>
</html>
```